Business card design needed

I need a business card design for a new online retail business based in Australia. I am unsure of the exact content of what I will be selling but it will be probably women's clothing, accessories, gym wear, gifts and maybe homeware linen. I am wanting a classy design that portrays the image of class/style/upmarket.

Target Market(s)

predominantely women - 20-50 age group

Industry/Entity Type

Retail

Contact Information for Business Card

Quietly Golden
Renata Calloway
Director
ABN 73418250964
17 Harrow Crescent Linfield Park NSW 2391
ph: +61 427 905 184
sales@quietlygolden.com.au

Logo Text

I am open for suggestions here

Requirements
Must have
• The design must be both sides of the card

```html
<!DOCTYPE html>
<html lang="en">
<head>
<meta charset="utf-8">
<title>Quietly Golden – Business Card</title>
<link rel="stylesheet" href="https://fonts.googleapis.com/css2?family=Arimo:wght@400&display=swap">
<style>
  :root {
    --page-bg: #e9ebe8;
    --card-white: #ffffff;
    --green-light: #b5d56a;
    --green-mid: #5ea845;
    --green-deep: #1e7a3a;
    --silver-light: #e6e6e6;
    --silver-dark: #8e8e8e;
    --text-grey: #555b5e;
    --name-green: #1b7a3a;
  }
  * { box-sizing: border-box; margin: 0; padding: 0; }
  html, body {
    width: 1200px; height: 900px; overflow: hidden;
    background: var(--page-bg);
    font-family: "Arimo", Arial, sans-serif;
  }
  .canvas {
    position: relative; width: 1200px; height: 900px;
  }
  .card {
    position: absolute; left: 280px; width: 640px; height: 380px;
    background: var(--card-white);
    overflow: hidden;
    box-shadow: 0 6px 18px rgba(0,0,0,0.18);
  }
  .card--front { top: 50px; }
  .card--back { top: 470px; }

  .card-front__bands { position: absolute; inset: 0; width: 100%; height: 100%; }
  .brand-lockup {
    position: absolute; left: 0; right: 0; top: 168px;
    display: flex; align-items: center; justify-content: center; gap: 14px;
  }
  .brand-lockup__dot {
    width: 26px; height: 26px; border-radius: 50%;
    background: var(--green-mid);
  }
  .brand-lockup__name {
    font-size: 44px; color: var(--text-grey); letter-spacing: 0.5px;
  }

  .back-badge {
    position: absolute; left: 52px; top: 24px; width: 188px; height: 148px;
    background: linear-gradient(180deg, var(--green-mid) 0%, var(--green-deep) 100%);
    display: flex; align-items: flex-end; justify-content: center;
    padding-bottom: 26px;
  }
  .back-badge__name { color: var(--card-white); font-size: 21px; }

  .contact { position: absolute; left: 56px; top: 188px; color: var(--text-grey); }
  .contact__name { font-size: 28px; color: var(--name-green); }
  .contact__role { font-size: 14px; margin-top: 8px; }
  .contact__address { font-size: 16px; line-height: 21px; margin-top: 20px; }
  .contact__lines { margin-top: 18px; font-size: 16px; line-height: 22px; }
  .contact__line { display: flex; align-items: center; gap: 8px; }
  .contact__icon { width: 14px; height: 14px; fill: var(--name-green); }
</style>
</head>
<body>
<main class="canvas">

  <section class="card card--front" aria-label="Card front">
    <svg class="card-front__bands" viewBox="0 0 640 380" preserveAspectRatio="none" aria-hidden="true">
      <defs>
        <linearGradient id="band-green" x1="0" y1="0" x2="1" y2="1">
          <stop offset="0" stop-color="var(--green-light)"/>
          <stop offset="1" stop-color="var(--green-deep)"/>
        </linearGradient>
        <linearGradient id="band-silver" x1="0" y1="0" x2="1" y2="0">
          <stop offset="0" stop-color="var(--silver-dark)"/>
          <stop offset="0.5" stop-color="var(--silver-light)"/>
          <stop offset="1" stop-color="var(--silver-dark)"/>
        </linearGradient>
      </defs>
      <rect width="640" height="380" fill="url(#band-green)"/>
      <ellipse cx="330" cy="200" rx="330" ry="300" fill="url(#band-silver)"/>
      <ellipse cx="318" cy="196" rx="318" ry="292" fill="var(--card-white)"/>
    </svg>
    <div class="brand-lockup">
      <span class="brand-lockup__dot"></span>
      <span class="brand-lockup__name">Quietly Golden</span>
    </div>
  </section>

  <section class="card card--back" aria-label="Card back">
    <div class="back-badge">
      <span class="back-badge__name">Quietly Golden</span>
    </div>
    <div class="contact">
      <p class="contact__name">Renata Calloway</p>
      <p class="contact__role">Director</p>
      <p class="contact__address">ABN 73418250964 17 Harrow Crescent<br>Linfield Park NSW 2391</p>
      <div class="contact__lines">
        <p class="contact__line">
          <svg class="contact__icon" viewBox="0 0 24 24" aria-hidden="true"><path d="M6.6 10.8a15 15 0 0 0 6.6 6.6l2.2-2.2a1 1 0 0 1 1-.25 11.4 11.4 0 0 0 3.6.57 1 1 0 0 1 1 1V20a1 1 0 0 1-1 1A17 17 0 0 1 3 4a1 1 0 0 1 1-1h3.5a1 1 0 0 1 1 1c0 1.25.2 2.45.57 3.57a1 1 0 0 1-.25 1z"/></svg>
          <span>+61 427 905 184</span>
        </p>
        <p class="contact__line">
          <svg class="contact__icon" viewBox="0 0 24 24" aria-hidden="true"><path d="M2 5h20v14H2z M2 5l10 8 10-8" fill="var(--name-green)"/><path d="M3 6l9 7 9-7" fill="none" stroke="#fff" stroke-width="1.6"/></svg>
          <span>sales@quietlygolden.com.au</span>
        </p>
      </div>
    </div>
  </section>

</main>
</body>
</html>
```